Web and Logo Design for eCommerce site

We're launching a sister brand and require a full design for the site.

The site must have an established feel and appeal to corporate and institutional buyers.
Updates

Just a note about the wireframe design:

The Search & Rescue / Coast Guard / NVDK, etc. in the header area aren't buttons or menu items, but rather just info (along the lines of a tagline).  Sort of a "who we serve" sort of thing.

Worth noting is that it's specifically geared towards LARGE BUYERS.  For example, a police force buying 200 headlamps and 85 pairs of gloves.  So they'll register + sign in and then add a bunch of items to a RFQ.

Aim for a professional, masculine design.

Target Market(s)

We will be selling outdoor gear to the military, law enforcement, fire and rescue and first responders.

Requirements
Must have
• We require:
- Logo (vector based)

Site:
- template page
* main site template, re-skinned version of our current site
* horizontal drop-down menu
- product listings page
* thumbnail view of products
- product details page
* including elements such as product image, color/size selector, descriptions and specs (again, based loosely on our current website)
- account management page
* illustrating basic data entry styles for text box, buttons, grid, etc.

The site needs to be given a responsive design, so 2 versions of each design should be presented for desktop + mobile views.

Additional funds are available if the designer is able to fully implement the designs into a responsive framework such as bootstrap.

Nice to have
• Clean, professional design similar to:

http://military.trailvexagear.com/gov/accessories/gloves.html

http://leaf.ombrivo.com/ProductFind.aspx?language=EN&category=Hardshell&subcat=Waterproof_Jackets

```html
<!DOCTYPE html>
<html lang="en">
<head>
<meta charset="utf-8">
<title>KanTrail – Northwind Field Outfitters</title>
<link href="https://fonts.googleapis.com/css2?family=Open+Sans:wght@400;600;700&display=swap" rel="stylesheet">
<style>
:root{
  --red:#a3122a;
  --wine:#8a1538;
  --grey-bar:#6d6d6d;
  --text:#333;
  --footer:#3b3b3b;
  --footer-deep:#262626;
  --line:#d8d8d8;
}
*{box-sizing:border-box;margin:0;padding:0}
html,body{width:800px;height:1200px;overflow:hidden}
body{font-family:"Open Sans",Arial,sans-serif;color:var(--text);background:#fff;position:relative}
.abs{position:absolute}

.site-header{left:80px;top:0;width:636px;height:60px;background:#fff;box-shadow:0 0 8px rgba(0,0,0,.18)}
.brand-mark{left:16px;top:14px;width:16px;height:16px;background:#777}
.brand-name{left:42px;top:6px;font-size:22px;color:var(--red);font-weight:400}
.brand-sub{left:42px;top:37px;font-size:10px;color:#222}
.header-quote{right:14px;top:13px;text-align:right;font-size:12px;line-height:16px;color:#333}

.login-bar{left:0;top:60px;width:800px;height:49px;background:var(--grey-bar)}
.login-icon{left:100px;top:12px;width:18px;height:22px}
.login-title{left:127px;top:13px;color:#fff;font-size:15px}
.login-input{top:18px;width:140px;height:15px;background:#fff;border:1px solid #ccc;font-size:7px;color:#888;padding:2px 7px}
.login-btn{left:579px;top:17px;width:82px;height:18px;background:var(--red);color:#fff;font-size:9px;text-align:center;line-height:18px;border:1px solid #c33}

.audience{left:0;top:109px;width:800px;height:25px}
.audience span{font-size:10px;color:var(--red);line-height:25px;position:absolute}

.main-nav{left:0;top:134px;width:800px;height:28px;background:var(--wine)}
.main-nav a{position:absolute;top:0;height:28px;line-height:28px;font-size:8px;color:#fff;text-decoration:none;text-align:center;border-right:1px solid rgba(255,255,255,.15)}
.main-nav a.active{background:#444}

.hero{left:66px;top:170px;width:660px;height:240px;background:#f2f2f2;box-shadow:0 2px 6px rgba(0,0,0,.15)}
.hero-photo{left:9px;top:13px;width:642px;height:217px;background:linear-gradient(90deg,#7a6f3a 0%,#8a8650 35%,#6f7d54 60%,#4f6a3c 100%)}
.hero-title{left:47px;top:53px;color:#fff;font-size:16px;letter-spacing:.3px}
.hero-copy{left:18px;top:86px;width:268px;color:#fff;font-size:9.5px;line-height:13.5px;text-align:right}
.hero-more{left:140px;top:149px;width:88px;height:27px;background:var(--red);color:#fff;font-size:9px;text-align:center;line-height:27px;border-radius:2px}
.hero-dots{left:247px;top:198px;display:flex;gap:3px}
.hero-dots i{width:7px;height:7px;border-radius:50%;background:#222;border:1px solid #fff}
.hero-dots i.on{background:var(--red)}

.range{left:65px;top:441px;width:156px;height:267px;border:1px solid #ddd;background:#fff}
.range-head{height:35px;background:var(--wine);color:#fff;font-size:12px;line-height:35px;padding-left:12px}
.range ul{list-style:none}
.range li{height:25px;line-height:25px;font-size:8px;padding-left:18px;border-bottom:1px solid #fff;background:#f3f3f3;position:relative;color:#333}
.range li:nth-child(odd){background:#fafafa}
.range li::before{content:"›";position:absolute;left:9px;top:1px;font-size:9px}
.range-foot{position:absolute;left:0;bottom:0;width:100%;height:5px;background:var(--wine)}

.offer{left:65px;top:729px;width:156px;height:206px;border:1px solid #ccc}
.offer-photo{left:1px;top:1px;width:152px;height:202px;background:linear-gradient(180deg,#5b86b8 0%,#cfdbe6 55%,#eef2f5 100%)}
.offer-title{left:11px;top:23px;color:#fff;font-size:12px;font-weight:600}
.offer-pct{left:91px;top:155px;color:var(--red);font-size:12px}
.offer-link{left:91px;top:177px;color:var(--wine);font-size:9px}

.products-title{left:255px;top:437px;font-size:15px;color:var(--red);font-weight:400}
.products-rule{left:255px;top:465px;width:477px;border-top:1px dotted #aaa}
.products-arrows{left:709px;top:441px;width:18px;height:10px}

.card{width:126px}
.card-img{width:126px;height:118px;border:1px solid var(--line);border-radius:2px;background:#fff;display:flex;align-items:center;justify-content:center}
.card-img div{width:82px;height:82px;border-radius:6px}
.card-name{margin-top:7px;font-size:9.5px;color:var(--red)}
.card-desc{margin-top:4px;font-size:7.5px;line-height:12px;color:#333}
.card-price{margin-top:4px;font-size:9px;color:var(--red)}
.card-btn{margin-top:4px;width:73px;height:19px;background:var(--wine);color:#fff;font-size:9px;font-weight:700;text-align:center;line-height:19px;border-radius:2px}

.footer{left:0;top:982px;width:800px;height:157px;background:var(--footer)}
.footer-base{left:0;top:1139px;width:800px;height:61px;background:var(--footer-deep)}
.f-head{color:#ddd;font-size:12px}
.nl-head{left:65px;top:17px;font-size:13px}
.nl-field{left:65px;top:48px;width:152px;height:20px;border:1px solid #999;background:#6a6a6a;border-radius:2px}
.nl-field span{position:absolute;left:11px;top:4px;font-size:7px;font-style:italic;color:#ddd}
.nl-btn{position:absolute;right:-1px;top:-1px;width:56px;height:20px;background:#d8401d;color:#fff;font-size:9.5px;text-align:center;line-height:20px;border-radius:0 2px 2px 0}
.chat{left:65px;top:94px;width:152px;height:34px;border:1px solid #aaa;background:#5a5a5a;border-radius:2px}
.chat-icon{position:absolute;left:12px;top:4px;width:24px;height:24px;border-radius:50%;background:#b23}
.chat span{position:absolute;left:52px;top:6px;color:#eee;font-size:14px}
.f-list{list-style:none}
.f-list li{font-size:7.5px;color:#ccc;position:relative;padding-left:12px}
.f-list li::before{content:"›";position:absolute;left:0;top:-1px}
.social{font-size:8.5px;color:#ddd;display:flex;align-items:center;gap:6px;justify-content:flex-end}
.social i{width:13px;height:13px;display:inline-block}
.copy{right:104px;top:20px;font-size:8px;color:#ccc}
.copy-x{right:104px;top:36px;font-size:8px;color:#ccc}
</style>
</head>
<body>

<header class="site-header abs">
  <div class="brand-mark abs"></div>
  <div class="brand-name abs">KanTrail</div>
  <div class="brand-sub abs">Northwind Field Outfitters</div>
  <div class="header-quote abs">“ Reliable Field Gear for<br>Crews Who Answer the Call”</div>
</header>

<section class="login-bar abs">
  <svg class="login-icon abs" viewBox="0 0 18 22"><path d="M4 10V6a5 5 0 0 1 10 0v4" fill="none" stroke="#ddd" stroke-width="2"/><rect x="1" y="10" width="16" height="12" rx="2" fill="#ccc"/></svg>
  <div class="login-title abs">Customer Login</div>
  <div class="login-input abs" style="left:255px">User Name</div>
  <div class="login-input abs" style="left:415px">Password</div>
  <div class="login-btn abs">LOGIN</div>
</section>

<div class="audience abs">
  <span style="left:103px">SEARCH AND RESCUE</span>
  <span style="left:247px">COAST GUARD</span>
  <span style="left:354px">NVDK</span>
  <span style="left:426px">FIRE</span>
  <span style="left:487px">MILITARY</span>
  <span style="left:570px">LAW ENFORCEMENT</span>
</div>

<nav class="main-nav abs">
  <a class="active" style="left:66px;width:81px">RESCUE GEAR</a>
  <a style="left:147px;width:94px">FOOTWEAR</a>
  <a style="left:241px;width:77px">CLOTHING</a>
  <a style="left:318px;width:161px">TENTS, MATS, SLEEPING BAGS</a>
  <a style="left:479px;width:100px">CAMPING GEAR</a>
  <a style="left:579px;width:94px">SNOW SPORTS</a>
  <a style="left:673px;width:73px;border-right:0">BRANDS</a>
</nav>

<section class="hero abs">
  <div class="hero-photo abs" role="img" aria-label="Hiker with a large backpack walking a trail through a green mountain valley">
    <div class="hero-title abs">LOREUM IPSUM DOLLAR</div>
    <p class="hero-copy abs">Sed ut perspiciatis unde omnis iste natus error sit voluptatem accusantium doloremque laudantium, totam rem aperiam.natus error sit voluptatem accusantium doloremque laudantium.</p>
    <div class="hero-more abs">More &gt;&gt;</div>
    <div class="hero-dots abs"><i class="on"></i><i></i><i></i><i></i></div>
  </div>
</section>

<aside class="range abs">
  <div class="range-head">Range of Products</div>
  <ul>
    <li>RCurabitur faucibus metus</li>
    <li>Nam Semper Elit Sed Lacus</li>
    <li>Fusce Semper Erat</li>
    <li>RCurabitur faucibus metus</li>
    <li>Nam Semper Elit Sed Lacus</li>
    <li>Fusce Semper Erat</li>
    <li>RCurabitur faucibus metus</li>
    <li>Nam Semper Elit Sed Lacus</li>
    <li>Fusce Semper Erat</li>
  </ul>
  <div class="range-foot"></div>
</aside>

<aside class="offer abs">
  <div class="offer-photo abs" role="img" aria-label="Skier in a blue jacket descending a snowy slope"></div>
  <div class="offer-title abs">Special Offers</div>
  <div class="offer-pct abs">30% Offer</div>
  <div class="offer-link abs">Clickhere &gt;&gt;</div>
</aside>

<h2 class="products-title abs">Our Products</h2>
<div class="products-rule abs"></div>
<svg class="products-arrows abs" viewBox="0 0 18 10"><path d="M7 0v10L1 5z M11 0v10l6-5z" fill="#111"/></svg>

<article class="card abs" style="left:255px;top:480px">
  <div class="card-img"><div role="img" aria-label="Black hooded shell jacket" style="background:#222"></div></div>
  <div class="card-name">Aliquam Ante Sed Tellus</div>
  <div class="card-desc">Pellentesque adipiscing gravida<br>sem quis cursus. Donec dapibus.</div>
  <div class="card-price">Price : $0.00</div>
  <div class="card-btn">Buy Now</div>
</article>
<article class="card abs" style="left:423px;top:480px">
  <div class="card-img"><div role="img" aria-label="Red and grey insulated jacket" style="background:#c8202a"></div></div>
  <div class="card-name">Aliquam Ante Sed Tellus</div>
  <div class="card-desc">Pellentesque adipiscing gravida<br>sem quis cursus. Donec dapibus.</div>
  <div class="card-price">Price : $0.00</div>
  <div class="card-btn">Buy Now</div>
</article>
<article class="card abs" style="left:590px;top:480px">
  <div class="card-img"><div role="img" aria-label="Orange waterproof match case with matches" style="background:#e0702a"></div></div>
  <div class="card-name">Aliquam Ante Sed Tellus</div>
  <div class="card-desc">Pellentesque adipiscing gravida<br>sem quis cursus. Donec dapibus.</div>
  <div class="card-price">Price : $0.00</div>
  <div class="card-btn">Buy Now</div>
</article>

<article class="card abs" style="left:255px;top:727px">
  <div class="card-img"><div role="img" aria-label="Blue and tan dome tent" style="background:linear-gradient(180deg,#2d4f7a,#c99a5a)"></div></div>
  <div class="card-name">Aliquam Ante Sed Tellus</div>
  <div class="card-desc">Pellentesque adipiscing gravida<br>sem quis cursus. Donec dapibus.</div>
  <div class="card-price">Price : $0.00</div>
  <div class="card-btn">Buy Now</div>
</article>
<article class="card abs" style="left:423px;top:727px">
  <div class="card-img"><div role="img" aria-label="Red backpack with trekking poles, boots and sleeping mat" style="background:linear-gradient(180deg,#d2282c,#6a7a74)"></div></div>
  <div class="card-name">Aliquam Ante Sed Tellus</div>
  <div class="card-desc">Pellentesque adipiscing gravida<br>sem quis cursus. Donec dapibus.</div>
  <div class="card-price">Price : $0.00</div>
  <div class="card-btn">Buy Now</div>
</article>
<article class="card abs" style="left:590px;top:727px">
  <div class="card-img"><div role="img" aria-label="Red portable camping grill with gas canister" style="background:linear-gradient(180deg,#c41c22,#333)"></div></div>
  <div class="card-name">Aliquam Ante Sed Tellus</div>
  <div class="card-desc">Pellentesque adipiscing gravida<br>sem quis cursus. Donec dapibus.</div>
  <div class="card-price">Price : $0.00</div>
  <div class="card-btn">Buy Now</div>
</article>

<footer class="footer abs">
  <div class="f-head nl-head abs">Newsletter</div>
  <div class="nl-field abs"><span>Email</span><div class="nl-btn">Subscribe</div></div>
  <div class="chat abs"><div class="chat-icon"></div><span>Live Chat</span></div>

  <div class="f-head abs" style="left:287px;top:13px">Quick Links</div>
  <ul class="f-list abs" style="left:288px;top:36px;line-height:14px">
    <li>RESCUE GEAR</li><li>FOOTWEAR</li><li>CLOTHING TENTS</li><li>MATS</li>
    <li>SLEEPING BAGS</li><li>CAMPING GEAR</li><li>SNOW SPORTS</li><li>BRANDS</li>
  </ul>

  <div class="f-head abs" style="left:428px;top:13px">Products</div>
  <ul class="f-list abs" style="left:429px;top:36px;line-height:16px">
    <li>SEARCH AND RESCUE</li><li>COAST GUARD</li><li>NVDK</li>
    <li>FIRE</li><li>MILITARY</li><li>LAW ENFORCEMENT</li>
  </ul>

  <div class="f-head abs" style="right:82px;top:12px;font-size:14px;color:#bbb">Connect with us</div>
  <div class="abs" style="left:560px;top:41px;width:80px;display:grid;row-gap:11px">
    <div class="social">Brimly<i style="background:#3b5a9a"></i></div>
    <div class="social">Orvana<i style="background:#2fa9e0"></i></div>
    <div class="social">RSS<i style="background:#f08a1c"></i></div>
  </div>
  <div class="abs" style="left:636px;top:41px;width:79px;display:grid;row-gap:11px">
    <div class="social">Zentro<i style="background:#1f6fae"></i></div>
    <div class="social">Quellio +1<i style="background:#3a8a3e"></i></div>
    <div class="social">Tessaly<i style="background:#cc2127"></i></div>
  </div>
</footer>

<div class="footer-base abs">
  <div class="copy abs">© 2014 KanTrail. All rights reserved</div>
  <div class="copy-x abs">X2</div>
</div>

</body>
</html>
```